Awesome business card design needed

We need a new business card design to go with our new logo.
We are a web development agency that specialises in highly complex back-end integrations as opposed to design, our customers are retailers, hotels, hospitals and any other organisation that has a large online marketing department.
Take a look at our website - www.brenoloft.com for some inspiration.
We want our new business cards to exude class, professionalism and style.
We are likely to choose a high-end card to print them on but we want the design of the card itself to really turn heads.
We have no specific colour requirements, the logo as you will see is a turquoise colour R89 G171 B167 #59aba7 but it can also be in white if you want to make the colour of the card something different.
The information on the card should be:
Name
Position
Tel
email
Potentially a double sided card could have our web address, twitter and FB links.

```html
<!DOCTYPE html>
<html lang="en">
<head>
<meta charset="utf-8">
<title>Brenoloft Business Card</title>
<link href="https://fonts.googleapis.com/css2?family=Roboto:wght@400;700&display=swap" rel="stylesheet">
<style>
  :root {
    --teal: #59aba7;
    --charcoal: #333333;
    --ink: #2b2b2b;
    --paper: #ffffff;
    --backdrop: #e9e9e7;
    --muted: #4a4a4a;
  }
  * { margin: 0; padding: 0; box-sizing: border-box; }
  html, body { width: 1200px; height: 720px; overflow: hidden; }
  body {
    background: var(--backdrop);
    font-family: "Roboto", Arial, sans-serif;
    display: flex;
    align-items: center;
    justify-content: center;
    gap: 40px;
  }
  .card {
    position: relative;
    width: 540px;
    height: 309px;
    overflow: hidden;
    box-shadow: 0 6px 18px rgba(0,0,0,0.18);
  }
  .card-front { background: var(--paper); }
  .card-back { background: var(--charcoal); }
  .swoosh { position: absolute; inset: 0; width: 100%; height: 100%; }
  .wordmark {
    font-family: "Roboto", Arial, sans-serif;
    font-weight: 700;
    color: var(--teal);
    line-height: 1;
    letter-spacing: 1px;
    white-space: nowrap;
  }
  .card-front .wordmark {
    position: absolute;
    left: 40px;
    top: 48px;
    font-size: 62px;
  }
  .identity {
    position: absolute;
    left: 58px;
    top: 158px;
    color: var(--muted);
  }
  .identity .name { font-size: 16px; font-weight: 700; color: var(--ink); }
  .identity .position { font-weight: 400; color: var(--teal); }
  .identity .address { margin-top: 8px; font-size: 12px; line-height: 1.35; }
  .contact-list {
    position: absolute;
    left: 385px;
    top: 162px;
    list-style: none;
    color: var(--paper);
    font-size: 12px;
    line-height: 1;
  }
  .contact-list li { display: flex; align-items: center; gap: 6px; margin-bottom: 7px; }
  .contact-list li:first-child { font-size: 14px; }
  .contact-list svg { width: 11px; height: 11px; flex: none; }
  .card-back .wordmark {
    position: absolute;
    left: 0; right: 0;
    top: 104px;
    text-align: center;
    font-size: 74px;
  }
  .follow {
    position: absolute;
    left: 0; right: 0;
    top: 198px;
    display: flex;
    justify-content: center;
    align-items: center;
    gap: 8px;
    color: var(--teal);
    font-weight: 700;
    font-size: 17px;
  }
  .social-mark {
    width: 28px; height: 28px;
    border-radius: 5px;
    background: var(--teal);
  }
  .social-mark.alt { background: #4b6ea8; }
  .web {
    position: absolute;
    left: 0; right: 0;
    top: 240px;
    text-align: center;
    color: var(--paper);
    font-size: 15px;
    letter-spacing: 1.5px;
  }
  .web strong { font-weight: 700; }
</style>
</head>
<body>
  <section class="card card-front">
    <svg class="swoosh" viewBox="0 0 540 309" preserveAspectRatio="none" aria-hidden="true">
      <path d="M0,288 C180,302 300,252 362,152 C402,92 470,72 540,64 V309 H0 Z" fill="var(--teal)"/>
      <path d="M0,276 C180,292 298,242 356,142 C396,82 470,58 540,50" fill="none" stroke="var(--charcoal)" stroke-width="5"/>
      <path d="M0,298 C170,306 290,272 345,215" fill="none" stroke="var(--charcoal)" stroke-width="5"/>
    </svg>
    <div class="wordmark">brenoloft</div>
    <div class="identity">
      <p class="name">Your Name, <span class="position">Position</span></p>
      <p class="address">Street Name, City Name<br>State Zip Code</p>
    </div>
    <ul class="contact-list">
      <li><svg viewBox="0 0 12 12"><path d="M3,1 L5,3.5 L4,5 C4.8,6.6 5.6,7.4 7,8 L8.5,7 L11,9 L10,11 C5,11 1,7 1,2 Z" fill="currentColor"/></svg>123-456-7890</li>
      <li><svg viewBox="0 0 12 12"><rect x="1" y="3" width="10" height="7" fill="currentColor"/><path d="M1,3 L6,7 L11,3" stroke="var(--teal)" fill="none"/></svg>info@brenoloft.com</li>
      <li><svg viewBox="0 0 12 12"><circle cx="6" cy="6" r="5" fill="none" stroke="currentColor" stroke-width="1.4"/><path d="M1,6 H11 M6,1 C3.5,4 3.5,8 6,11 M6,1 C8.5,4 8.5,8 6,11" stroke="currentColor" fill="none"/></svg>www.brenoloft.com</li>
    </ul>
  </section>

  <section class="card card-back">
    <div class="wordmark">brenoloft</div>
    <div class="follow">
      <span>Follow Us On:</span>
      <span class="social-mark"></span>
      <span class="social-mark alt"></span>
    </div>
    <p class="web">www.<strong>brenoloft</strong>.com</p>
  </section>
</body>
</html>
```